Business card for my new company (Accounting firm)

I need a business card for my new business Brightwell Advisory and Ledger SA. Our services are accounting, tax, audit and financial management. Our customers are small companies, start-ups and new companies. The final design has to show financial security, trust and growth. Please find our logo attached to the business card. Text for the business card: Brightwell Advisory and Ledger SA Tomas Varenholt Director and Founder Certified Accountant Tel. 022 418 57 34 tv@clairevalconseil.ch www.clairevalconseil.ch Rue des Vergières 27 1201 Geneva
Target Market(s)
Our customers are small companies, start-ups and new companies.
Industry/Entity Type
Finance And Accounting
Contact Information for Business Card
Claireval Conseil et Comptes SA
Tomas Varenholt
Directeur et Fondateur
Expert-comptable diplômé
Tél. 022 418 57 34
tv@clairevalconseil.ch
www.clairevalconseil.ch
Rue des Vergières 27
1201 Genève

```html
<!DOCTYPE html>
<html lang="fr">
<head>
<meta charset="utf-8">
<title>Claireval Conseil et Comptes SA – Carte de visite</title>
<link href="https://fonts.googleapis.com/css2?family=Roboto:wght@400;500;700&display=swap" rel="stylesheet">
<style>
  :root {
    --page-bg: #e4e5e7;
    --blue-light: #2ba3da;
    --blue-deep: #1b6ea6;
    --blue-name: #1f5f99;
    --mark-blue: #2a8fca;
    --ink: #3a3d42;
    --ink-soft: #55595f;
    --card-white: #f7f7f7;
    --on-blue: #ffffff;
  }
  * { box-sizing: border-box; margin: 0; padding: 0; }
  html, body { width: 1200px; height: 726px; overflow: hidden; }
  body {
    background: var(--page-bg);
    font-family: "Roboto", Arial, sans-serif;
    position: relative;
  }
  .card {
    position: absolute;
    top: 210px;
    width: 520px;
    height: 306px;
    border-radius: 3px;
    box-shadow: 0 6px 18px rgba(0,0,0,0.12);
    overflow: hidden;
  }
  /* Front */
  .card-front {
    left: 56px;
    background: linear-gradient(135deg, var(--blue-light) 0%, var(--blue-deep) 100%);
    color: var(--on-blue);
    display: flex;
    flex-direction: column;
    align-items: center;
    justify-content: center;
  }
  .brand {
    display: flex;
    align-items: center;
    gap: 14px;
  }
  .brand-square {
    width: 30px;
    height: 30px;
    background: var(--on-blue);
  }
  .brand-name {
    font-weight: 500;
    font-size: 30px;
    letter-spacing: 1px;
    color: var(--on-blue);
  }
  .brand-tagline {
    margin-top: 8px;
    font-weight: 500;
    font-size: 15px;
    letter-spacing: 3px;
    text-transform: uppercase;
    color: var(--on-blue);
  }
  .front-web {
    margin-top: 34px;
    font-size: 15px;
    font-weight: 500;
    color: var(--on-blue);
  }
  /* Back */
  .card-back {
    left: 624px;
    background: var(--card-white);
    color: var(--ink);
  }
  .person {
    position: absolute;
    left: 36px;
    top: 44px;
  }
  .person-name {
    font-weight: 700;
    font-size: 20px;
    color: var(--blue-name);
  }
  .person-role {
    margin-top: 6px;
    font-size: 12.5px;
    line-height: 1.3;
    color: var(--ink-soft);
  }
  .address {
    position: absolute;
    left: 36px;
    top: 170px;
    font-size: 13px;
    line-height: 1.35;
    color: var(--ink);
  }
  .contacts {
    position: absolute;
    left: 36px;
    top: 214px;
    list-style: none;
    font-size: 13px;
    line-height: 1.35;
    color: var(--ink);
  }
  .contacts li { display: flex; align-items: center; gap: 10px; height: 18px; }
  .contacts svg { width: 12px; height: 12px; fill: var(--blue-name); flex: none; }
  .back-brand {
    position: absolute;
    right: 30px;
    top: 104px;
    text-align: left;
  }
  .back-brand .brand-square { background: var(--mark-blue); width: 26px; height: 26px; }
  .back-brand .brand-name { color: var(--ink); font-size: 26px; }
  .back-brand .brand-tagline { color: var(--ink); font-size: 11px; letter-spacing: 2px; margin-top: 6px; padding-left: 40px; }
</style>
</head>
<body>
  <section class="card card-front" aria-label="Recto">
    <div class="brand">
      <span class="brand-square"></span>
      <span class="brand-name">CLAIREVAL</span>
    </div>
    <div class="brand-tagline">Conseil et Comptes</div>
    <div class="front-web">www.clairevalconseil.ch</div>
  </section>

  <section class="card card-back" aria-label="Verso">
    <div class="person">
      <h1 class="person-name">Tomas Varenholt</h1>
      <p class="person-role">Directeur et Fondateur<br>Expert-comptable diplômé</p>
    </div>

    <p class="address">Rue des Vergières 27<br>1201 Genève</p>

    <ul class="contacts">
      <li>
        <svg viewBox="0 0 24 24" aria-hidden="true"><path d="M6.6 10.8a15.1 15.1 0 0 0 6.6 6.6l2.2-2.2c.3-.3.7-.4 1-.2 1.1.4 2.3.6 3.6.6.6 0 1 .4 1 1V20c0 .6-.4 1-1 1A17 17 0 0 1 3 4c0-.6.4-1 1-1h3.5c.6 0 1 .4 1 1 0 1.3.2 2.5.6 3.6.1.3 0 .7-.2 1z"/></svg>
        022 418 57 34
      </li>
      <li>
        <svg viewBox="0 0 24 24" aria-hidden="true"><path d="M2 5h20v14H2zm2 2v.4l8 5 8-5V7zm0 2.7V17h16V9.7l-8 5z"/></svg>
        tv@clairevalconseil.ch
      </li>
      <li>
        <svg viewBox="0 0 24 24" aria-hidden="true"><path d="M12 2a10 10 0 1 0 0 20 10 10 0 0 0 0-20zm6.9 6h-3a15 15 0 0 0-1.3-3.9A8 8 0 0 1 18.9 8zM12 4c.8 1.2 1.5 2.5 1.9 4h-3.8c.4-1.5 1.1-2.8 1.9-4zM4.3 14a8 8 0 0 1 0-4h3.4a16 16 0 0 0 0 4zm.8 2h3a15 15 0 0 0 1.3 3.9A8 8 0 0 1 5.1 16zm3-8h-3a8 8 0 0 1 4.3-3.9A15 15 0 0 0 8.1 8zM12 20c-.8-1.2-1.5-2.5-1.9-4h3.8c-.4 1.5-1.1 2.8-1.9 4zm2.3-6H9.7a14 14 0 0 1 0-4h4.6a14 14 0 0 1 0 4zm.3 5.9a15 15 0 0 0 1.3-3.9h3a8 8 0 0 1-4.3 3.9zm1.7-5.9a16 16 0 0 0 0-4h3.4a8 8 0 0 1 0 4z"/></svg>
        www.clairevalconseil.ch
      </li>
    </ul>

    <div class="back-brand">
      <div class="brand">
        <span class="brand-square"></span>
        <span class="brand-name">CLAIREVAL</span>
      </div>
      <div class="brand-tagline">Conseil et Comptes</div>
    </div>
  </section>
</body>
</html>
```